Lumo Medical Aesthetics - Service Flyer

We are looking to have a friend-fold flyer designed that outlines all of the services offered. I am able to provide pricing on all products and outline of services.

We have had a flyer made in the past and the colours were black and white to go with the logo and keep it simple. We would prefer to keep these colours, but are open to adding in a couple of extra complimentary colours which would match our clinic. I have attached the original flyer that was created as well as our logo.

Target Market(s)

Women aged 25-65

Requirements
Must have
• Our website is www.lumoclinicra.example
• 555-284-7162
• Facebook: lumoclinicra
• Instagram @lumoclinicra
• Services to be included are:
• Some pricing has not been listed, but will update shortly
• Velquin $8/unit
• Renza $10/unit
• Dermal Fillers
• (Cheeks, lips, jawline, chin, temples, under eyes, smile lines, smokers lines)
• 1ml syringe $475
• Mini Lip Plump $250
• Non-Surgical Face Lift $1100
• (Choice of 3 areas, eg. lips, jaw contouring, cheeks)
• Facial Treatments:
• Personalized Facial $85
• Organic Facial -$100
• Deep Cleansing / Acne Facial - $120
• Gel Peel (20% Glycolic/10% Lactic/3.2pH) - $75
• Dermaplaning $120
• Microdermabrasion $120
• Microneedling $250
• Microneedling (package of 3) $600
• Platelet-Rich Plasma (PRP) Facial $400
• Platinum Facial (Dermaplaning + Microneedling) $350
• LED Light Therapy $45
• High Frequency $45
• Skin Consultation (Free)
• Permanent Make-Up:
• Microblading $350
• Microblading Touch-Up $50
• Lashline Enhancement - Top Lashline $300
• Lashline Enhancement - Bottom Lashline $350
• Touch-Up Top/Bottom Lashline $50
• Lip Blush $450
• Lip Blush Touch-up $50
• Tattoo Removal $200 (per session)
• Cosmetic Treatments:
• Classic Eyelash Extensions $99
• Classic Fill $45
• Hybrid Eyelash Extensions $120
• Hybrid Fill $55
• Eyelash Lift & Tint $75
• Teeth Whitening $125
• Organic Teeth Whitening $150
• Medical Aesthetics Treatments:
• Laser Hair Removal $35 and up (per session)
• (Consultation and patch test required for all clients)
• Microneedling for Stretch Marks and Scars - $250 +
• Platelet-Rich Plasma (PRP) Hair Restoration - $500
• Scalp Micropigmentation - $500 and up
• The brivolux / laser hair removal write-up should be replaced with the following:
• We believe in providing only the best for our clients. We specialize in a number of Medical Aesthetics Treatments to address common skin and anti-aging concerns among our clients. All of our treatments are non-invasive, highly effective and affordable. Our services are performed by certified professionals, using clinically proven equipment and products approved and certified through Health Canada.
• We take pride in the high calibre experience we offer our clients and believe that choosing the appropriate certified professional that can deliver the results you desire, is of primary importance. Lumo employs highly qualified professionals, operating under Dr. Malcolm Dunstan, Board Certified Plastic Surgeon acting as the Medical Director, as well as partners of the Tandem Medical team.

```html
<!DOCTYPE html>
<html lang="en">
<head>
<meta charset="utf-8">
<title>Lumo Medical Aesthetics – Service Flyer</title>
<link href="https://fonts.googleapis.com/css2?family=Open+Sans:wght@300;400&family=PT+Sans+Narrow:wght@400;700&display=swap" rel="stylesheet">
<style>
  :root{
    --page:#bdbdbd;
    --slate:#6b6b6b;
    --ink:#100707;
    --gold:#d19b14;
    --cream:#f8f4ea;
    --white:#ffffff;
    --muted:#7a7a7a;
    --text-light:#ffffff;
    --text-dark:#333333;
  }
  *{box-sizing:border-box;margin:0;padding:0}
  html,body{width:841px;height:1200px;overflow:hidden;background:var(--page)}
  body{position:relative;font-family:"PT Sans Narrow","Arial Narrow",sans-serif}
  .panel{position:absolute;overflow:hidden}
  .photo{position:absolute}

  /* outside spread */
  .about{left:62px;top:52px;width:233px;height:504px;background:var(--slate)}
  .about .photo{left:0;top:0;width:233px;height:166px;background:linear-gradient(135deg,#c9b08e,#e8d4bd 45%,#a9b17a)}
  .about-title{position:absolute;left:25px;top:178px;width:205px;font-family:"Open Sans",sans-serif;font-weight:400;font-size:19px;line-height:25px;color:var(--gold);white-space:nowrap}
  .about-copy{position:absolute;left:25px;top:236px;width:200px;font-size:9.2px;line-height:16.1px;color:var(--text-light)}
  .about-copy p+p{margin-top:16px}

  .contact{left:295px;top:52px;width:240px;height:504px;background:var(--ink)}
  .contact-lines{position:absolute;left:24px;bottom:73px;display:flex;align-items:flex-end;gap:8px}
  .contact-line{writing-mode:vertical-rl;transform:rotate(180deg);font-family:"Open Sans",sans-serif;font-weight:400;font-size:23px;line-height:24px;color:var(--muted);white-space:nowrap}
  .contact-icons{position:absolute;left:23px;top:443px;display:flex;gap:8px}
  .contact-icons svg{width:24px;height:24px}

  .cover{left:535px;top:52px;width:240px;height:504px;background:var(--cream)}
  .cover .photo{left:0;top:0;width:240px;height:363px;background:linear-gradient(160deg,#e9e6e2,#d9c3ab 50%,#f1efec)}
  .cover-band{position:absolute;left:0;top:363px;width:240px;height:10px;background:var(--gold)}
  .brand{position:absolute;left:0;top:418px;width:240px;text-align:center;font-family:"Open Sans",sans-serif;font-weight:400;font-size:15px;letter-spacing:1px;color:var(--ink);line-height:18px}

  /* inside spread */
  .heading{font-weight:700;font-size:17px;line-height:20px;color:var(--gold)}
  .price-list{list-style:none;font-size:10.6px;line-height:15.3px}
  .price-row{display:flex;align-items:baseline;white-space:nowrap}
  .price-row .leader{flex:1;border-bottom:.6px solid currentColor;margin:0 2px;transform:translateY(-3px);opacity:.8}
  .price-row small{font-size:6.5px}
  .note{font-size:6.4px;line-height:9px;margin:-1px 0 2px}

  .services{left:62px;top:623px;width:240px;height:505px;background:var(--slate);color:var(--text-light)}
  .services .heading{position:absolute;left:18px;top:17px}
  .services .list-main{position:absolute;left:18px;top:41px;width:206px}
  .services .photo{left:0;top:158px;width:240px;height:107px;background:linear-gradient(120deg,#e4d2c7,#f1e8e2 50%,#c6a991)}
  .services .facials-heading{position:absolute;left:18px;top:272px}
  .services .list-facials{position:absolute;left:18px;top:296px;width:203px}

  .makeup{left:302px;top:623px;width:240px;height:505px;background:var(--ink);color:var(--text-light)}
  .makeup .heading{position:absolute;left:13px;top:17px}
  .makeup .list-pmu{position:absolute;left:14px;top:41px;width:208px}
  .makeup .cosmetic-heading{position:absolute;left:13px;top:172px}
  .makeup .list-cosmetic{position:absolute;left:14px;top:194px;width:203px}
  .makeup .photo{left:0;top:297px;width:240px;height:208px;background:linear-gradient(150deg,#e9e7e4,#d6b9a5 55%,#a9c4d6)}

  .medical{left:542px;top:623px;width:233px;height:505px;background:var(--white);color:var(--text-dark)}
  .medical .heading{position:absolute;left:10px;top:17px;white-space:nowrap}
  .medical .list-med{position:absolute;left:10px;top:41px;width:210px}
  .medical .photo{left:0;top:132px;width:233px;height:373px;background:linear-gradient(170deg,#d9c6c6,#e2bfa8 50%,#dcd2d9)}
</style>
</head>
<body>

<section class="panel about">
  <div class="photo" role="img" aria-label="Photo of a woman relaxing at a spa with a flower in her hair"></div>
  <h2 class="about-title">Quality Matters:<br>The Lumo Experience</h2>
  <div class="about-copy">
    <p>We believe in providing only the best for our clients. We specialize in a number of Medical Aesthetics Treatments to address common skin and anti-aging concerns among our clients. All of our treatments are non-invasive, highly effective and affordable. Our services are performed by certified professionals, using clinically proven equipment and products approved and certified through Health Canada.</p>
    <p>We take pride in the high calibre experience we offer our clients and believe that choosing the appropriate certified professional that can deliver the results you desire, is of primary importance. Lumo employs highly qualified professionals, operating under Dr. Malcolm Dunstan, Board Certified Plastic Surgeon acting as the Medical Director, as well as partners of the Tandem Medical team.</p>
  </div>
</section>

<section class="panel contact">
  <div class="contact-lines">
    <span class="contact-line">555-284-7162</span>
    <span class="contact-line">www.lumoclinicra.example</span>
    <span class="contact-line">info@lumoclinicra.example</span>
    <span class="contact-line">lumoclinicra</span>
    <span class="contact-line">@lumoclinicra</span>
  </div>
  <div class="contact-icons">
    <svg viewBox="0 0 24 24" aria-label="Phone"><circle cx="12" cy="12" r="11" fill="none" stroke="#7a7a7a" stroke-width="1.4"/><path d="M8 7l2 0 1 3-1.5 1a7 7 0 0 0 3.5 3.5l1-1.5 3 1 0 2c-5 1-10-4-9-9z" fill="none" stroke="#7a7a7a" stroke-width="1.2"/></svg>
    <svg viewBox="0 0 24 24" aria-label="Website"><circle cx="12" cy="12" r="11" fill="none" stroke="#7a7a7a" stroke-width="1.4"/><circle cx="12" cy="12" r="7" fill="none" stroke="#7a7a7a" stroke-width="1"/><ellipse cx="12" cy="12" rx="3" ry="7" fill="none" stroke="#7a7a7a" stroke-width="1"/><path d="M5 12h14M6 9h12M6 15h12" stroke="#7a7a7a" stroke-width="1"/></svg>
    <svg viewBox="0 0 24 24" aria-label="Email"><circle cx="12" cy="12" r="11" fill="none" stroke="#7a7a7a" stroke-width="1.4"/><rect x="8" y="6" width="8" height="12" fill="none" stroke="#7a7a7a" stroke-width="1.1"/><path d="M8 6l8 12M16 6l-8 12" stroke="#7a7a7a" stroke-width="1"/></svg>
    <svg viewBox="0 0 24 24" aria-label="Social page"><rect x="2" y="2" width="20" height="20" rx="3" fill="#7a7a7a"/></svg>
    <svg viewBox="0 0 24 24" aria-label="Social profile"><rect x="2" y="2" width="20" height="20" rx="3" fill="#7a7a7a"/></svg>
  </div>
</section>

<section class="panel cover">
  <div class="photo" role="img" aria-label="Photo of a smiling woman in a white robe"></div>
  <div class="cover-band"></div>
  <div class="brand">LUMO<br>MEDICAL AESTHETICS</div>
</section>

<section class="panel services">
  <h2 class="heading">Services</h2>
  <ul class="price-list list-main">
    <li class="price-row">Velquin<span class="leader"></span>$8/unit</li>
    <li class="price-row">Renza<span class="leader"></span>$10/unit</li>
    <li class="price-row">Dermal Fillers</li>
    <li class="note">(cheeks, lips, jawline, chin, temples, under eyes, smile lines, smokers lines)</li>
    <li class="price-row">1ml syringe<span class="leader"></span>$475</li>
    <li class="price-row">Mini Lip Plump<span class="leader"></span>$250</li>
    <li class="price-row">Non-Surgical Face Lift<span class="leader"></span>$1100</li>
    <li class="note">(Choice of 3 areas, eg. lips, jaw contouring, cheeks)</li>
  </ul>
  <div class="photo" role="img" aria-label="Photo of eyelash extensions being applied with tweezers"></div>
  <h2 class="heading facials-heading">Facial Treatments:</h2>
  <ul class="price-list list-facials">
    <li class="price-row">Personalized Facial<span class="leader"></span>$85</li>
    <li class="price-row">Organic Facial<span class="leader"></span>$100</li>
    <li class="price-row">Deep Cleansing / Acne Facial<span class="leader"></span>$120</li>
    <li class="price-row">Gel Peel (20% Glycolic/10% Lactic/3.2pH)<span class="leader"></span>$75</li>
    <li class="price-row">Dermaplaning<span class="leader"></span>$120</li>
    <li class="price-row">Microdermabrasion<span class="leader"></span>$120</li>
    <li class="price-row">Microneedling<span class="leader"></span>$250</li>
    <li class="price-row">Microneedling (package of 3)<span class="leader"></span>$600</li>
    <li class="price-row">Platelet-Rich Plasma (PRP) Facial<span class="leader"></span>$400</li>
    <li class="price-row">Platinum Facial&nbsp;<small>(Dermaplaning + Microneedling)</small><span class="leader"></span>$350</li>
    <li class="price-row">LED Light Therapy<span class="leader"></span>$45</li>
    <li class="price-row">High Frequency<span class="leader"></span>$45</li>
    <li class="price-row">Skin Consultation (Free)</li>
  </ul>
</section>

<section class="panel makeup">
  <h2 class="heading">Permanent Make-Up:</h2>
  <ul class="price-list list-pmu">
    <li class="price-row">Microblading<span class="leader"></span>$350</li>
    <li class="price-row">Microblading Touch-Up<span class="leader"></span>$50</li>
    <li class="price-row">Lashline Enhancement - Top Lashline<span class="leader"></span>$300</li>
    <li class="price-row">Lashline Enhancement - Bottom Lashline<span class="leader"></span>$350</li>
    <li class="price-row">Touch-Up Top/Bottom Lashline<span class="leader"></span>$50</li>
    <li class="price-row">Lip Blush<span class="leader"></span>$450</li>
    <li class="price-row">Lip Blush Touch-up<span class="leader"></span>$50</li>
    <li class="price-row">Tattoo Removal&nbsp;<small>(per session)</small><span class="leader"></span>$200</li>
  </ul>
  <h2 class="heading cosmetic-heading">Cosmetic Treatments:</h2>
  <ul class="price-list list-cosmetic">
    <li class="price-row">Eyelash Extensions&nbsp;<small>(Classic)</small><span class="leader"></span>$99</li>
    <li class="price-row">Fill&nbsp;<small>(Classic)</small><span class="leader"></span>$45</li>
    <li class="price-row">Eyelash Extensions&nbsp;<small>(Hybrid)</small><span class="leader"></span>$120</li>
    <li class="price-row">Fill&nbsp;<small>(Hybrid)</small><span class="leader"></span>$55</li>
    <li class="price-row">Eyelash Lift &amp; Tint<span class="leader"></span>$75</li>
    <li class="price-row">Teeth Whitening $125 / Organic $150</li>
  </ul>
  <div class="photo" role="img" aria-label="Photo of a woman receiving a facial treatment with a gloved practitioner"></div>
</section>

<section class="panel medical">
  <h2 class="heading">Medical Aesthetics Treatments:</h2>
  <ul class="price-list list-med">
    <li class="price-row">Laser Hair Removal (and up per session)<span class="leader"></span>$35</li>
    <li class="note">(Consultation and patch test required for all clients)</li>
    <li class="price-row">Microneedling for Stretch Marks and Scars +<span class="leader"></span>$250</li>
    <li class="price-row">Platelet-Rich Plasma (PRP) Hair Restoration<span class="leader"></span>$500</li>
    <li class="price-row">Scalp Micropigmentation - &nbsp;and up<span class="leader"></span>$500</li>
  </ul>
  <div class="photo" role="img" aria-label="Photo of a woman with smooth skin touching her face"></div>
</section>

</body>
</html>
```